Professional & attention grabbing.

A business card design, front and back. I already have a logo I will attach, but I am open to something new as well.
Things to include:
Name:
Title:
Phone:
Email:
Wanting something that is professional but attention grabbing.
Also we do a lot of work using drones on natural gas pipelines (leading the future)if you want to include any of that. I'm open to ideas.
Target Market(s)
Natural gas transmission industry / greenhouse gas mitigation industry
Industry/Entity Type
Business
Colors
Designer to choose colors to be used in the design.
Look and feel
Each slider illustrates characteristics of the customer's brand and the style your logo design should communicate.

```html
<!DOCTYPE html>
<html lang="en">
<head>
<meta charset="utf-8">
<title>Kestrel Pipeline Surveys — Business Card</title>
<link rel="stylesheet" href="https://fonts.googleapis.com/css2?family=Roboto+Condensed:wght@300;400;700&display=swap">
<style>
  :root {
    --stage: #e7e4df;
    --card-white: #ffffff;
    --brand-red: #c01f26;
    --brand-red-dark: #9e1a20;
    --charcoal: #3c3d40;
    --slate: #5b5c60;
    --text-dark: #2e2e30;
    --shadow: rgba(0, 0, 0, 0.18);
  }
  * { margin: 0; padding: 0; box-sizing: border-box; }
  html, body {
    width: 1200px; height: 950px; overflow: hidden;
    background: var(--stage);
    font-family: "Roboto Condensed", Arial, sans-serif;
  }
  .stage { position: relative; width: 1200px; height: 950px; }
  .card {
    position: absolute; left: 250px; width: 700px; height: 400px;
    box-shadow: 0 10px 24px var(--shadow);
    overflow: hidden;
  }
  .card-front { top: 55px; background: var(--card-white); }
  .card-back { top: 495px; background: var(--brand-red); }

  .edge-band { position: absolute; left: 0; top: 0; width: 260px; height: 400px; }

  .brand-lockup {
    position: absolute; left: 120px; top: 205px;
    display: flex; align-items: center; gap: 16px;
  }
  .brand-square { width: 58px; height: 58px; background: var(--brand-red); }
  .brand-name {
    font-weight: 700; color: var(--slate);
    font-size: 46px; line-height: 1; letter-spacing: 1px; text-transform: uppercase;
  }
  .brand-tagline {
    font-weight: 700; color: var(--slate);
    font-size: 15px; letter-spacing: 2px; text-transform: uppercase; margin-top: 6px;
  }

  .contact-block {
    position: absolute; right: 42px; top: 48px; text-align: right;
  }
  .person-name {
    color: var(--brand-red); font-weight: 700; font-size: 30px; letter-spacing: 1px;
  }
  .person-title {
    color: var(--text-dark); font-weight: 400; font-size: 20px; margin-bottom: 20px;
  }
  .contact-line {
    display: flex; justify-content: flex-end; align-items: center; gap: 10px;
    color: var(--text-dark); font-size: 20px; font-weight: 400; line-height: 30px;
  }
  .contact-icon { width: 18px; height: 18px; flex: none; }

  .back-lockup {
    position: absolute; right: 60px; bottom: 60px;
    display: flex; align-items: center; gap: 14px;
  }
  .back-square { width: 44px; height: 44px; background: var(--card-white); }
  .back-name {
    color: var(--card-white); font-weight: 700; font-size: 34px;
    letter-spacing: 1px; text-transform: uppercase;
  }
  .back-web {
    position: absolute; left: 40px; bottom: 32px;
    color: var(--card-white); font-size: 18px; font-weight: 300; font-style: italic;
  }
</style>
</head>
<body>
<main class="stage">
  <section class="card card-front" aria-label="Business card front">
    <svg class="edge-band" viewBox="0 0 260 400" aria-hidden="true">
      <polygon points="0,0 60,0 60,210 230,400 0,400" fill="var(--charcoal)"/>
      <polygon points="60,210 92,210 260,400 230,400" fill="var(--brand-red)"/>
      <polygon points="0,120 24,120 24,400 0,400" fill="var(--slate)"/>
    </svg>

    <div class="brand-lockup">
      <div class="brand-square"></div>
      <div>
        <div class="brand-name">Kestrel</div>
        <div class="brand-tagline">Pipeline Surveys</div>
      </div>
    </div>

    <div class="contact-block">
      <div class="person-name">DANA WHITFIELD</div>
      <div class="person-title">CEO/Founder</div>
      <div class="contact-line">555 014 2386
        <svg class="contact-icon" viewBox="0 0 18 18" aria-hidden="true">
          <path d="M4 2l3 3-1.6 2a9 9 0 0 0 5.6 5.6L13 11l3 3-2 2C8 16 2 10 2 4z" fill="var(--brand-red)"/>
        </svg>
      </div>
      <div class="contact-line">dana@kestrelsurveys.com
        <svg class="contact-icon" viewBox="0 0 18 18" aria-hidden="true">
          <rect x="1" y="4" width="16" height="11" rx="1.5" fill="var(--brand-red)"/>
          <path d="M2 5l7 5 7-5" stroke="#fff" stroke-width="1.4" fill="none"/>
        </svg>
      </div>
      <div class="contact-line">www.kestrelsurveys.com
        <svg class="contact-icon" viewBox="0 0 18 18" aria-hidden="true">
          <circle cx="9" cy="9" r="8" fill="var(--brand-red)"/>
          <ellipse cx="9" cy="9" rx="3.2" ry="7" stroke="#fff" stroke-width="1.2" fill="none"/>
          <line x1="1.5" y1="9" x2="16.5" y2="9" stroke="#fff" stroke-width="1.2"/>
        </svg>
      </div>
    </div>
  </section>

  <section class="card card-back" aria-label="Business card back">
    <div class="back-lockup">
      <div class="back-square"></div>
      <div class="back-name">Kestrel</div>
    </div>
    <div class="back-web">www.kestrelsurveys.com</div>
  </section>
</main>
</body>
</html>
```